Vibrant, yet professional, stationery set and other designs required.

I need to source a fantastic designer for a new project as part of my company using a new logo designed via sketch harbor.

**UPDATE** I am not looking for just 'fine' design that will suffice. I am looking for something great.

We are a life assurance brokerage based in Dublin, Ireland and BrightRoost.ie is our new website aimed at providing services for young families in Ireland. We are hoping to be the 'Velro' level of service providers in this area and I am looking for the quality of design to reflect this :-) Hopefully that makes sense!

I have a preference for straight lines over curves and waves.

I need...

1. Business card
2. Letterhead
3. Banner (for printing - 76cm X 305cm)
4. Car branding for KORVA 9 (2014 sport model) I believe the templates are freely available online.

Target Market(s)

Parents in Ireland - Aged 27 to 50.

Industry/Entity Type

Financial Planning

Colors

Designer to choose colors to be used in the design.

Requirements
Must have
• All of the items listed in the description above. I like clean, bright, legible, vibrant and professional design.
Should not have
• No silly or 'cheap' looking designs. This is a professional company looking to provide a professional service.

```html
<!DOCTYPE html>
<html lang="en">
<head>
<meta charset="utf-8">
<title>BrightRoost.ie Business Card</title>
<link rel="stylesheet" href="https://fonts.googleapis.com/css2?family=Roboto:wght@400;500;700&family=Roboto+Condensed:wght@500;700&display=swap">
<style>
  :root {
    --bg: #b9b9b9;
    --orange: #f08219;
    --paper: #f4f4f4;
    --grey: #8d9699;
    --grey-dark: #858e92;
    --text: #4a4a4a;
    --white: #ffffff;
  }
  * { margin: 0; padding: 0; box-sizing: border-box; }
  html, body { width: 1200px; height: 960px; overflow: hidden; }
  body {
    position: relative;
    background: var(--bg);
    font-family: "Roboto", sans-serif;
  }
  .card {
    position: absolute;
    left: 320px;
    width: 600px;
    height: 343px;
  }
  .card--front {
    top: 105px;
    background: var(--orange);
  }
  .card--back {
    top: 493px;
    background: var(--paper);
  }
  .front-brand {
    position: absolute;
    top: 192px;
    left: 0;
    width: 100%;
    text-align: center;
    color: var(--white);
    font-family: "Roboto", sans-serif;
    font-weight: 700;
    font-size: 56px;
    letter-spacing: -1px;
  }
  .front-web {
    position: absolute;
    top: 290px;
    left: 0;
    width: 100%;
    text-align: center;
    color: var(--white);
    font-size: 14px;
    letter-spacing: 6px;
  }
  .back-brand {
    position: absolute;
    top: 150px;
    left: 50px;
    width: 250px;
    text-align: center;
    color: var(--grey);
    font-family: "Roboto", sans-serif;
    font-weight: 700;
    font-size: 36px;
    letter-spacing: -0.5px;
  }
  .divider {
    position: absolute;
    left: 327px;
    top: 77px;
    width: 1px;
    height: 196px;
    background: #c9cccd;
  }
  .contact {
    position: absolute;
    left: 354px;
    top: 75px;
    color: var(--text);
  }
  .contact__name {
    font-family: "Roboto Condensed", sans-serif;
    font-weight: 700;
    font-size: 20px;
    color: var(--orange);
    line-height: 24px;
  }
  .contact__role {
    font-family: "Roboto Condensed", sans-serif;
    font-weight: 500;
    font-size: 15px;
    color: var(--grey);
    line-height: 20px;
    margin-bottom: 9px;
  }
  .contact__address {
    font-size: 14.5px;
    line-height: 18px;
    margin-bottom: 9px;
  }
  .contact__list { list-style: none; }
  .contact__list li {
    display: flex;
    align-items: center;
    font-size: 14.5px;
    line-height: 19px;
  }
  .contact__list svg {
    width: 13px;
    height: 13px;
    margin-right: 10px;
    fill: var(--orange);
    flex: none;
  }
  .band {
    position: absolute;
    left: 0;
    bottom: 0;
    width: 600px;
    height: 23px;
  }
</style>
</head>
<body>
  <section class="card card--front">
    <div class="front-brand">BrightRoost.ie</div>
    <div class="front-web">www.brightroost.ie</div>
  </section>

  <section class="card card--back">
    <div class="back-brand">BrightRoost.ie</div>
    <div class="divider"></div>
    <div class="contact">
      <div class="contact__name">LIAM DARCY</div>
      <div class="contact__role">CEO/FOUNDER</div>
      <div class="contact__address">42 Harrow Quay<br>Dunmore, Leinster 10482</div>
      <ul class="contact__list">
        <li><svg viewBox="0 0 16 16"><path d="M3 1l3 3-1.6 2.2a9 9 0 0 0 5.4 5.4L12 10l3 3-2 2C6.5 15 1 9.5 1 3z"/></svg>615 280 4471</li>
        <li><svg viewBox="0 0 16 16"><path d="M4 0h8a1 1 0 0 1 1 1v14a1 1 0 0 1-1 1H4a1 1 0 0 1-1-1V1a1 1 0 0 1 1-1zm1 2v10h6V2zm3 11a1 1 0 1 0 0 2 1 1 0 0 0 0-2z"/></svg>872 534 1906</li>
        <li><svg viewBox="0 0 16 16"><path d="M4 1h8v4H4zM1 6h14v7h-3v2H4v-2H1zm4 5v3h6v-3z"/></svg>439 761 2058</li>
        <li><svg viewBox="0 0 16 16"><path d="M1 3h14v10H1zm1.5 1.3L8 8.5l5.5-4.2V12h-11z"/></svg>hello@brightroost.ie</li>
        <li><svg viewBox="0 0 16 16"><circle cx="8" cy="8" r="7"/><path d="M1 8h14M8 1c3 3 3 11 0 14M8 1c-3 3-3 11 0 14" stroke="#f4f4f4" stroke-width="1.2" fill="none"/></svg>www.brightroost.ie</li>
      </ul>
    </div>
    <svg class="band" viewBox="0 0 600 23" preserveAspectRatio="none">
      <polygon points="0,0 390,0 384,23 0,23" fill="var(--orange)"/>
      <polygon points="394,0 600,0 600,23 388,23" fill="var(--grey-dark)"/>
    </svg>
  </section>
</body>
</html>
```